Maranoola Wines - web page for new Australian wine label

We need a landing page for our wine company. Maranoola is a family owned company, we grow the gapes, and make the wine in the Clare valley. Daniel Whitlock is the winemaker and is well known for his style, which is all about the fruit flavour rather than wood or age influences. Maranoola is Abriginal for 2 hills and a water source. We hand pick, hand plunge, foot crush resulting in elegant wine. Little to no additives, minimal filtering, single vineyard wines. Handcrafted with small releases of only the best fruit from carefully selected rows and bunches. The Clare valley is located two hours North of Adelaide, is known for cool climate and slow ripening, resulting in wines that have an elegant mouth feel, with bright colour and outstanding flavours. Our Brookmere vineyard has a Eastern aspect, gathering morning sun and escaping the hot afternoons, and in our opinion is on of the prettiest valleys in the world. Only 1000 cases per annum of the very best handpicked fruit, from the best rows. We hope you enjoy the Maranoola style, the reds are lighter in colour, fruit driven palate, more old world influence and the Riesling is on the dry side with fresh citrus. Minimal additives and filtering, our aim was to make wine with minimal influence from wine making. Handcrafted wines.

Target Market(s)

females 18 - 60 are the ones that buy 70 percent of wine, so whilst men are also a target, its the ladies we seek to appeal to.

Industry/Entity Type

It Company

Number of Pages Required

4 page

Font styles to use
Serif

Requirements
Must have
• Eye catching front page that makes me feel like i am ordering from quality company, that cares for what they do. Easy to use ordering, and delivery instructions.
• postage is $14.90 per case Australia wide.
• www.maranoolawines-example.com
Nice to have
• I want to see a fun and family oriented business that cares for the wine, we dont make a lot, its buckets and feet. But its wine made wanting to be the best in the world, we dont cut corners on quality. Handcrafted
Should not have
• dont really have any thoughts here, looking for all ideas

```html
<!DOCTYPE html>
<html lang="en">
<head>
<meta charset="utf-8">
<title>Maranoola Wines</title>
<link href="https://fonts.googleapis.com/css2?family=Alegreya:wght@400;700&family=Montserrat:wght@600;700&family=Open+Sans:wght@400;600;700&family=Oswald:wght@500&family=Roboto:wght@300&display=swap" rel="stylesheet">
<style>
:root{
  --blue:#0d5bb5;
  --ink:#222;
  --body:#555;
  --line:#e3e3e3;
  --red:#d7263d;
  --paper:#fff;
  --soft:#f4f4f4;
  --map:#ececec;
}
*{margin:0;padding:0;box-sizing:border-box}
html,body{width:1200px;height:2740px;overflow:hidden;background:var(--paper)}
body{position:relative;font-family:"Open Sans",sans-serif;color:var(--body)}
.abs{position:absolute}
a{color:inherit;text-decoration:none}

/* header */
.site-header{position:absolute;left:0;top:0;width:1200px;height:128px;border-bottom:4px solid var(--blue)}
.brand{position:absolute;left:131px;top:36px;font-family:"Alegreya",serif;font-size:50px;color:var(--blue);line-height:1}
.cases-pill{position:absolute;left:860px;top:25px;width:208px;height:38px;border-radius:19px;background:var(--blue);color:#fff;font-size:13px;display:flex;align-items:center;justify-content:center}
.cases-pill b{margin:0 4px}
.main-nav{position:absolute;top:82px;left:542px;display:flex;font-weight:700;font-size:14px;color:var(--ink)}
.main-nav a{display:block;height:46px;padding-top:4px;text-align:center}
.main-nav .active{color:var(--blue);border-bottom:6px solid var(--blue)}

/* hero */
.hero{position:absolute;left:0;top:132px;width:1200px;height:535px;background:
  radial-gradient(ellipse 30% 35% at 62% 78%,#5b2a4a 0%,rgba(91,42,74,0) 100%),
  radial-gradient(ellipse 25% 30% at 20% 70%,#8a4a22 0%,rgba(138,74,34,0) 100%),
  radial-gradient(ellipse 22% 40% at 40% 15%,#7a3a1a 0%,rgba(122,58,26,0) 100%),
  linear-gradient(180deg,#1e120c,#2a1810 60%,#140c08)}
.hero-title{position:absolute;top:168px;width:100%;text-align:center;font-family:"Montserrat",sans-serif;font-weight:700;font-size:54px;color:#fff;letter-spacing:1px}
.hero-sub{position:absolute;top:236px;width:100%;text-align:center;font-family:"Roboto",sans-serif;font-weight:300;font-size:33px;color:#fff}
.hero-arrow{position:absolute;top:215px}

/* method cards */
.method{position:absolute;top:661px;width:294px;height:303px;background:#fff;border:1px solid var(--line);border-top:6px solid var(--blue);text-align:center}
.method-photo{position:absolute;left:49px;top:-86px;width:196px;height:196px;border-radius:50%;background:#fff;padding:4px;border-bottom:5px solid var(--blue)}
.method-photo span{display:block;width:100%;height:100%;border-radius:50%}
.method h3{position:absolute;top:128px;width:100%;font-weight:700;font-size:16px;color:var(--ink);letter-spacing:.5px}
.method p{position:absolute;top:159px;left:20px;right:20px;font-size:12px;line-height:22px;color:var(--body)}
.btn{display:inline-block;background:var(--blue);color:#fff;font-weight:700;font-size:10px;border-radius:20px;text-align:center;letter-spacing:.3px}
.method .btn{position:absolute;left:96px;top:231px;width:102px;height:37px;line-height:37px}

/* features */
.bottle-art{position:absolute;left:126px;top:1110px;width:190px;height:410px;border-radius:8px;background:
  radial-gradient(ellipse 45% 8% at 50% 98%,#ddd 0%,rgba(221,221,221,0) 100%),
  linear-gradient(180deg,#8a1420 0%,#2a1a1e 14%,#1a1518 60%,#121012 100%)}
.price-badge{position:absolute;left:233px;top:1146px;width:74px;height:74px;border-radius:50%;background:var(--red);border:4px solid #fff;box-shadow:0 0 0 2px var(--red);color:#fff;font-family:"Oswald",sans-serif;font-size:19px;display:flex;align-items:center;justify-content:center}
.section-title{position:absolute;left:427px;top:1110px;font-family:"Alegreya",serif;font-weight:700;font-size:34px;color:var(--ink)}
.feature{position:absolute;left:431px;width:620px;height:90px}
.feature-icon{position:absolute;left:0;top:0;width:80px;height:80px;border-radius:50%;border:2px solid var(--blue);display:flex;align-items:center;justify-content:center}
.feature h4{position:absolute;left:108px;top:0;font-weight:600;font-size:14px;color:var(--blue)}
.feature p{position:absolute;left:108px;top:28px;width:510px;font-size:12px;line-height:22px;color:var(--body)}

/* welcome */
.welcome{position:absolute;left:0;top:1583px;width:1200px;height:410px;background:linear-gradient(180deg,#151515,#0b0b0b)}
.welcome h2{position:absolute;left:131px;top:60px;font-family:"Alegreya",serif;font-weight:700;font-size:33px;color:#fff}
.welcome p{position:absolute;left:131px;width:475px;font-size:12px;line-height:22px;color:#e8e8e8}
.welcome .btn{position:absolute;left:131px;top:296px;width:102px;height:36px;line-height:36px}
.video{position:absolute;left:628px;top:68px;width:438px;height:268px;background:linear-gradient(135deg,#4a3f3a,#7a5a5a 50%,#5a2430)}
.video-bar{position:absolute;left:0;bottom:0;width:100%;height:26px;background:#f1f1f1;display:flex;align-items:center;font-size:8px;color:#333}

/* delivery */
.world-map{position:absolute;left:131px;top:2086px;width:585px;height:290px;background:var(--map);border-radius:6px}
.map-label{position:absolute;left:500px;top:2266px;font-family:"Alegreya",serif;font-size:24px;color:#222}
.delivery-head{position:absolute;left:767px;top:2084px;font-weight:600;font-size:17px;color:#333}
.delivery-price{position:absolute;left:767px;top:2106px;font-family:"Oswald",sans-serif;font-weight:500;font-size:38px;color:var(--red)}
.delivery-price small{font-family:"Open Sans",sans-serif;font-size:12px;color:#555;margin-left:4px}
.quote{position:absolute;left:792px;top:2192px;width:282px;font-size:11px;line-height:19px;color:#555}
.quote-mark{position:absolute;left:780px;top:2184px;font-family:"Alegreya",serif;font-size:22px;color:#333}
.avatar{position:absolute;left:792px;top:2290px;width:70px;height:70px;border-radius:50%;background:linear-gradient(#b08a70,#6b4a3a)}
.reviewer{position:absolute;left:887px;top:2302px;font-size:13px;color:var(--blue)}
.stars{position:absolute;left:887px;top:2330px;display:flex;gap:2px;align-items:center;font-size:11px;color:#666;font-style:italic}
.stars i{display:block;width:14px;height:14px;background:var(--blue)}

/* footer */
.site-footer{position:absolute;left:0;top:2467px;width:1200px;height:273px;background:var(--soft);border-top:6px solid var(--blue)}
.footer-brand{position:absolute;left:131px;top:48px;font-family:"Alegreya",serif;font-size:50px;color:var(--blue)}
.socials{position:absolute;left:162px;top:135px;display:flex;gap:7px}
.socials span{width:26px;height:26px;border-radius:50%}
.copyright{position:absolute;left:173px;top:181px;font-size:11px;color:#333}
.footer-col h5{position:absolute;top:50px;font-family:"Alegreya",serif;font-weight:700;font-size:15px;color:#222}
.quick-links{position:absolute;left:400px;top:83px;list-style:none;font-size:11px;line-height:24px;color:#444}
.post{position:absolute;left:542px;width:274px;height:64px;background:#fff;border:1px solid var(--line)}
.post-thumb{position:absolute;left:0;top:0;width:81px;height:62px;background:linear-gradient(135deg,#6a5040,#a07b5a)}
.post p{position:absolute;left:90px;top:10px;font-size:10px;color:#444}
.post em{position:absolute;left:90px;top:34px;font-style:normal;font-size:10px;color:var(--blue)}
.contact-row{position:absolute;left:876px;font-size:11px;line-height:20px;color:#444;display:flex;gap:12px}
.contact-row svg{flex:none;margin-top:4px}
</style>
</head>
<body>

<header class="site-header">
  <div class="brand">Maranoola</div>
  <div class="cases-pill">Only <b>1000</b> Cases per Annum</div>
  <nav class="main-nav">
    <a class="active" style="width:86px">Home</a>
    <a style="width:96px">About Us</a>
    <a style="width:104px">Services</a>
    <a style="width:90px">Products</a>
    <a style="width:76px">Blog</a>
    <a style="width:90px">Contact</a>
  </nav>
</header>

<section class="hero" role="img" aria-label="Photo of a glass of red wine, grapes and autumn vine leaves on a dark table">
  <h1 class="hero-title">Family Owned Wine</h1>
  <p class="hero-sub">Very best handpicked fruit, from the best rows</p>
  <svg class="hero-arrow" style="left:108px" width="26" height="74" viewBox="0 0 26 74"><polyline points="24,2 2,37 24,72" fill="none" stroke="#fff" stroke-width="1.5"/></svg>
  <svg class="hero-arrow" style="left:1066px" width="26" height="74" viewBox="0 0 26 74"><polyline points="2,2 24,37 2,72" fill="none" stroke="#fff" stroke-width="1.5"/></svg>
</section>

<article class="method" style="left:131px">
  <div class="method-photo"><span role="img" aria-label="Photo of a worker hand picking grapes in the vineyard" style="background:radial-gradient(circle at 60% 65%,#b0553a 0%,rgba(176,85,58,0) 45%),linear-gradient(170deg,#5f7040,#7a6a3a 55%,#4a3a2a)"></span></div>
  <h3>HAND PICK</h3>
  <p>There are many variations of passages Lorem Ipsum available, but the majority have suffered alteration in some form...</p>
  <a class="btn">READ MORE</a>
</article>
<article class="method" style="left:453px">
  <div class="method-photo"><span role="img" aria-label="Photo of two winemakers standing by barrels in the cellar" style="background:radial-gradient(circle at 50% 60%,#2a2624 0%,rgba(42,38,36,0) 50%),linear-gradient(170deg,#8a8070,#5a4e44 60%,#3a302a)"></span></div>
  <h3>HAND PLUNGE</h3>
  <p>There are many variations of passages Lorem Ipsum available, but the majority have suffered alteration in some form...</p>
  <a class="btn">READ MORE</a>
</article>
<article class="method" style="left:772px">
  <div class="method-photo"><span role="img" aria-label="Photo of feet crushing dark grapes in a vat" style="background:radial-gradient(circle at 45% 40%,#7a5a6a 0%,rgba(122,90,106,0) 45%),linear-gradient(170deg,#3a2a34,#24181e 60%,#1a1216)"></span></div>
  <h3>FOOT CRUSH</h3>
  <p>There are many variations of passages Lorem Ipsum available, but the majority have suffered alteration in some form...</p>
  <a class="btn">READ MORE</a>
</article>

<div class="bottle-art" role="img" aria-label="Product photo of two bottles of red wine with white labels"></div>
<div class="price-badge">$120</div>
<svg class="abs" style="left:300px;top:1210px" width="135" height="270" viewBox="0 0 135 270">
  <g fill="none" stroke="#cfcfcf" stroke-width="1.5">
    <polyline points="0,132 112,30 130,30"/>
    <polyline points="0,132 130,132"/>
    <polyline points="0,132 112,251 130,251"/>
  </g>
  <circle cx="112" cy="30" r="4" fill="#cfcfcf"/><circle cx="112" cy="132" r="4" fill="#cfcfcf"/><circle cx="112" cy="251" r="4" fill="#cfcfcf"/>
</svg>
<h2 class="section-title">Product Features</h2>

<div class="feature" style="top:1180px">
  <div class="feature-icon"><svg width="40" height="40" viewBox="0 0 40 40" fill="none" stroke="#0d5bb5" stroke-width="2"><circle cx="14" cy="12" r="5"/><circle cx="26" cy="12" r="5"/><circle cx="20" cy="20" r="5"/><circle cx="10" cy="21" r="5"/><circle cx="30" cy="21" r="5"/><circle cx="15" cy="29" r="5"/><circle cx="25" cy="29" r="5"/><circle cx="20" cy="36" r="3"/><path d="M20 7 L22 1"/></svg></div>
  <h4>Assumenda est, omnis dolor repellendus eveniet ut et voluptates</h4>
  <p>Nam libero tempore, cum soluta nobis est eligendi optio cumque nihil impedit quo minus id quod maxime placeat facere possimus,saepe eveniet...</p>
</div>
<div class="feature" style="top:1302px">
  <div class="feature-icon"><svg width="40" height="40" viewBox="0 0 40 40" fill="none" stroke="#0d5bb5" stroke-width="2"><path d="M10 2h6v8l3 5v23H7V15l3-5z"/><rect x="9" y="20" width="8" height="9"/><path d="M25 12h10c0 8-2 12-5 12s-5-4-5-12zM30 24v12M26 37h8"/></svg></div>
  <h4>Assumenda est, omnis dolor repellendus eveniet ut et voluptates</h4>
  <p>Nam libero tempore, cum soluta nobis est eligendi optio cumque nihil impedit quo minus id quod maxime placeat facere possimus,saepe eveniet...</p>
</div>
<div class="feature" style="top:1421px">
  <div class="feature-icon"><svg width="40" height="40" viewBox="0 0 40 40" fill="none" stroke="#0d5bb5" stroke-width="2"><ellipse cx="20" cy="20" rx="14" ry="17"/><path d="M8 10h24M6 20h28M8 30h24M20 14v12"/><rect x="17" y="16" width="6" height="8"/></svg></div>
  <h4>Assumenda est, omnis dolor repellendus eveniet ut et voluptates</h4>
  <p>Nam libero tempore, cum soluta nobis est eligendi optio cumque nihil impedit quo minus id quod maxime placeat facere possimus,saepe eveniet...</p>
</div>

<section class="welcome">
  <h2>Welcome to Maranoola</h2>
  <p style="top:114px">Sed ut perspiciatis unde omnis iste natus error sit voluptatem dolore laudantium, totam rem aperiam, eaque ipsa quae ab illo inventore veritatis et quasi architecto beatae vitae dicta sunt explicabo. Nemo enim ipsam voluptatem quia voluptas sit asperiatur aut odit aut fugit, sed quia consequuntur...</p>
  <p style="top:218px">Doloremque laudantium, totam rem aperiam, eaque ipsa quae ab illo inventore veritatis et quasi architecto beatae vitae dicta sunt explicabo...</p>
  <a class="btn">READ MORE</a>
  <div class="video" role="img" aria-label="Video still of two children crushing grapes in a red tub">
    <svg class="abs" style="left:194px;top:100px" width="52" height="52" viewBox="0 0 52 52"><circle cx="26" cy="26" r="24" fill="rgba(0,0,0,.35)" stroke="#fff" stroke-width="2"/><polygon points="20,15 37,26 20,37" fill="#fff"/></svg>
    <div class="video-bar">
      <svg style="margin:0 8px" width="8" height="9" viewBox="0 0 8 9"><polygon points="0,0 8,4.5 0,9" fill="#222"/></svg>
      <span>10:00/00:03</span>
      <span style="margin-left:14px;width:200px;height:3px;background:#d33;display:block"></span>
      <span style="width:60px;height:3px;background:#bbb;display:block"></span>
      <svg style="margin-left:30px" width="12" height="10" viewBox="0 0 12 10"><polygon points="0,3 3,3 7,0 7,10 3,7 0,7" fill="#222"/></svg>
      <span style="margin-left:6px;width:40px;height:3px;background:#d33;display:block"></span>
    </div>
  </div>
</section>

<div class="world-map" role="img" aria-label="Light grey world map"></div>
<svg class="abs" style="left:608px;top:2254px" width="40" height="52" viewBox="0 0 40 52"><path d="M20 2a17 17 0 0 1 17 17c0 13-17 31-17 31S3 32 3 19A17 17 0 0 1 20 2z" fill="#0d5bb5"/><circle cx="20" cy="19" r="11" fill="#fff"/><rect x="13" y="15" width="9" height="7" fill="#0d5bb5"/><path d="M22 17h3l3 3v2h-6z" fill="#0d5bb5"/></svg>
<div class="map-label">Maranoola</div>

<div class="delivery-head">DELIVERY CHARGE IS</div>
<div class="delivery-price">$14.90<small>/ PER CASE AUSTRALIA WIDE...</small></div>
<div class="abs" style="left:767px;top:2171px;width:300px;height:1px;background:var(--line)"></div>
<div class="quote-mark">&ldquo;</div>
<p class="quote">Leo knows exactly how to accomplish and complete experienced, professional, and knows how it all works. In my case, with Harbor Trust, he had to represent my interest yet get it all done in the best way</p>
<div class="avatar" role="img" aria-label="Portrait photo of the reviewer"></div>
<div class="reviewer">-Leo Fairbank</div>
<div class="stars"><i></i><i></i><i></i><i></i><i></i><span style="margin-left:8px">(88 reviews)</span></div>
<svg class="abs" style="left:1052px;top:2332px" width="16" height="10" viewBox="0 0 16 10"><polyline points="4,1 1,5 4,9" fill="none" stroke="#999"/><polyline points="12,1 15,5 12,9" fill="none" stroke="#999"/></svg>

<footer class="site-footer">
  <div class="footer-brand">Maranoola</div>
  <div class="socials"><span style="background:#3b5998"></span><span style="background:#0e76a8"></span><span style="background:#f29200"></span><span style="background:#55acee"></span><span style="background:#cd201f"></span></div>
  <div class="copyright">Copyrights &copy; Maranoola .2017</div>

  <div class="footer-col"><h5 style="left:400px">Quick Links</h5></div>
  <ul class="quick-links"><li>Home</li><li>About Us</li><li>Services</li><li>Products</li><li>Blog</li><li>Contact</li></ul>

  <div class="footer-col"><h5 style="left:542px">Recent Post</h5></div>
  <div class="post" style="top:82px"><div class="post-thumb" role="img" aria-label="Photo of family at the winery"></div><p>Cum soluta nobis est eligen opt...</p><em>Posted on 23 Feb 2017</em></div>
  <div class="post" style="top:151px"><div class="post-thumb" role="img" aria-label="Photo of family at the winery"></div><p>Cum soluta nobis est eligen opt...</p><em>Posted on 23 Feb 2017</em></div>

  <div class="footer-col"><h5 style="left:876px">Contact info</h5></div>
  <div class="contact-row" style="top:80px"><svg width="12" height="15" viewBox="0 0 12 15"><path d="M6 1a5 5 0 0 1 5 5c0 4-5 8-5 8S1 10 1 6a5 5 0 0 1 5-5z" fill="none" stroke="#666" stroke-width="1.3"/><circle cx="6" cy="6" r="1.8" fill="#666"/></svg><span>Produced by Peter Alden<br>27 Ridgeview Lane<br>Brookmere South Australia 5999</span></div>
  <div class="contact-row" style="top:156px"><svg width="12" height="12" viewBox="0 0 12 12"><path d="M2 1l3 0 1 3-2 1c1 2 2 3 3 3l1-2 3 1 0 3c-6 0-9-3-9-9z" fill="#666"/></svg><span>Phone: 555-014-7781</span></div>
  <div class="contact-row" style="top:196px"><svg width="12" height="10" viewBox="0 0 12 10"><rect x="0.5" y="0.5" width="11" height="9" fill="#666"/><polyline points="1,1 6,5 11,1" fill="none" stroke="#fff"/></svg><span>Email: info@maranoola-example.com</span></div>
</footer>

</body>
</html>
```